Stylish Business Cards Wanted

- DOUBLE SIDED Design Required -

High end, edgy cards for a corporate and personal stylist. Must include logo,
Name: Belinda Harwick
Title: Director and Stylist
telephone : +61 8 7142 5809
email: belinda@theloombriefing.example
website: theloombriefing.example
Tag: Corporate Workwear & Uniform Specialist | Personal Stylist
Would like nice icons for telephone, email, website

Target Market(s)

Businesses wanting stylish uniforms, people wanting stylish wardrobes

Industry/Entity Type

Corporate Workwear Stylist

Contact Information for Business Card

I would like black, white and gold foiling incorporated in the design - possibly a touch of the other colours on my branding guide attached Name: Belinda Harwick Title: Director and Stylist telephone : +61 8 7142 5809 email: belinda@theloombriefing.example website: theloombriefing.example Tag: Corporate Workwear & Uniform Specialist | Personal Stylist Would like nice icons for telephone, email, website

Font styles to use
Other font styles liked:
• Raleway

Colors

Designer to choose colors to be used in the design.

Requirements
Must have
• Gold foil accents

```html
<!DOCTYPE html>
<html lang="en">
<head>
<meta charset="utf-8">
<title>The Loom Briefing — Business Cards</title>
<link rel="stylesheet" href="https://fonts.googleapis.com/css2?family=Raleway:wght@500;600;700&family=Courgette&display=swap">
<style>
  :root {
    --backdrop: #2e2e30;
    --card: #1d1d20;
    --gold: #e2bb55;
    --gold-deep: #c99a2e;
    --white: #ffffff;
    --pink: #e5157a;
    --ink: #1d1d20;
  }
  * { box-sizing: border-box; margin: 0; padding: 0; }
  html, body { width: 799px; height: 1200px; overflow: hidden; }
  body {
    background: var(--backdrop);
    font-family: "Raleway", Arial, sans-serif;
    position: relative;
  }
  .card {
    position: absolute;
    left: 80px;
    width: 640px;
    height: 366px;
    background: var(--card);
    border-radius: 22px;
    overflow: hidden;
    box-shadow: 0 10px 28px rgba(0,0,0,.45);
  }
  .card--front { top: 90px; }
  .card--back { top: 700px; }

  .front-logo {
    position: absolute;
    inset: 0;
    display: flex;
    flex-direction: column;
    align-items: center;
    justify-content: center;
    color: var(--gold);
    font-weight: 700;
    text-transform: uppercase;
    text-align: center;
    gap: 14px;
  }
  .front-logo__name { font-size: 58px; letter-spacing: 4px; line-height: 1; }
  .front-logo__mark {
    width: 120px; height: 6px; background: var(--gold);
  }

  .back-logo {
    position: absolute;
    left: 36px; top: 48px;
    color: var(--white);
    font-weight: 700;
    text-transform: uppercase;
    font-size: 30px;
    letter-spacing: 2px;
    line-height: 1.05;
  }
  .holder { position: absolute; left: 36px; top: 168px; }
  .holder__name {
    font-family: "Courgette", cursive;
    color: var(--gold);
    font-size: 27px;
  }
  .holder__title { color: var(--white); font-size: 14px; font-weight: 500; margin-top: 4px; }

  .tagline {
    position: absolute;
    right: 30px; top: 120px;
    text-align: right;
    font-family: "Courgette", cursive;
    color: var(--white);
    font-size: 15px;
    line-height: 1.35;
  }
  .tagline__dot {
    display: inline-block; width: 5px; height: 5px;
    border-radius: 50%; background: var(--pink);
    margin-left: 8px; vertical-align: middle;
  }

  .contacts {
    position: absolute;
    left: 350px; top: 196px;
    list-style: none;
    color: var(--white);
    font-size: 15px;
    font-weight: 500;
  }
  .contacts li { display: flex; align-items: center; gap: 12px; height: 24px; }
  .contacts svg { width: 15px; height: 15px; flex: none; }

  .bands { position: absolute; left: 0; bottom: 0; width: 640px; height: 100px; }

  .handle {
    position: absolute;
    left: 356px; bottom: 32px;
    display: flex; align-items: center; gap: 10px;
    color: var(--ink);
    font-size: 16px; font-weight: 600;
  }
  .handle__dot { width: 14px; height: 14px; border-radius: 50%; background: var(--ink); }
</style>
</head>
<body>

  <section class="card card--front" aria-label="Card front">
    <div class="front-logo">
      <span class="front-logo__name">The Loom<br>Briefing</span>
      <span class="front-logo__mark"></span>
    </div>
  </section>

  <section class="card card--back" aria-label="Card back">
    <div class="back-logo">The Loom<br>Briefing</div>

    <div class="holder">
      <p class="holder__name">Belinda Harwick</p>
      <p class="holder__title">Director and Stylist</p>
    </div>

    <p class="tagline">
      Corporate Workwear<span class="tagline__dot"></span><br>
      &amp; Uniform Specialist<br>
      Personal Stylist<span class="tagline__dot"></span>
    </p>

    <ul class="contacts">
      <li>
        <svg viewBox="0 0 16 16" fill="none" stroke="var(--gold)" stroke-width="1.5"><circle cx="8" cy="8" r="7"/><path d="M5.5 4.5l1.5 0 .6 2-1 .8a5 5 0 0 0 2.1 2.1l.8-1 2 .6v1.5c-3.8.5-6.5-2.2-6-6z" fill="var(--gold)" stroke="none"/></svg>
        +61 8 7142 5809
      </li>
      <li>
        <svg viewBox="0 0 16 16" fill="none" stroke="var(--gold)" stroke-width="1.5"><rect x="1.5" y="3.5" width="13" height="9" rx="1"/><path d="M1.5 4l6.5 5 6.5-5"/></svg>
        belinda@theloombriefing.example
      </li>
      <li>
        <svg viewBox="0 0 16 16" fill="none" stroke="var(--gold)" stroke-width="1.3"><circle cx="8" cy="8" r="6.5"/><ellipse cx="8" cy="8" rx="3" ry="6.5"/><path d="M1.5 8h13M2.5 5h11M2.5 11h11"/></svg>
        www.theloombriefing.example
      </li>
    </ul>

    <svg class="bands" viewBox="0 0 640 100" aria-hidden="true">
      <rect x="0" y="10" width="300" height="8" fill="var(--pink)"/>
      <path d="M270 18 L300 4 Q306 0 316 0 L640 0 L640 100 L270 100 Z" fill="var(--gold)"/>
    </svg>

    <div class="handle">
      <span class="handle__dot"></span>
      /theloombriefing101
    </div>
  </section>

</body>
</html>
```